High-end construction company needs a business card design

We need a modern looking business card that draws people in, is memorable and looks so good people will want to sick it on their fridges.
On the first side what is needed are:
Logo
My name - Tomasz Brelwik
Title - Managing Director
Website - www.varkelt.co.uk
Email - tomasz@varkelt.co.uk
Telephone - 020 5194 6281
Mobile - 07845139072
On the back side was is needed is a list of all the services we provide:
-Kitchen Renovations
-Bathroom Renovations
-House Renovations
-Garage Conversions
-Extensions
-Loft Conversions
-Conservatories
-Carpentry
-Tiling
-Electrical
-Plumbing & Heating
-Bricklaying
-Landscaping
-Decorating
-Plastering
We would like the colours to be the same shades as on the logo with grey or black for the words.
Target Market(s)
Anyone who needs building work done
Contact Information for Business Card
This business card is for a construction company which strives to deliver excellent service and quality.
The look and feel of the card should represent this.
Requirements
Must have
- On the first side what is needed are:
Logo
My name - Tomasz Brelwik
Title - Managing Director
Website - www.varkelt.co.uk
Email - tomasz@varkelt.co.uk
Telephone - 020 5194 6281
Mobile - 07845139072
Nice to have
- Cool looking features

```html
<!DOCTYPE html>
<html lang="en">
<head>
<meta charset="utf-8">
<title>Varkelt Construction Ltd – Business Card</title>
<link href="https://fonts.googleapis.com/css2?family=Arimo:wght@400;700&display=swap" rel="stylesheet">
<style>
  :root {
    --brand-green: #76bc43;
    --brand-green-dark: #3f8f3a;
    --ink: #2b2b2b;
    --ink-soft: #555555;
    --paper: #fafafa;
    --backdrop: #dcdcdc;
    --divider: #bdbdbd;
  }
  * { box-sizing: border-box; margin: 0; padding: 0; }
  html, body {
    width: 1200px; height: 930px; overflow: hidden;
    background: var(--backdrop);
    font-family: "Arimo", Arial, sans-serif;
  }
  .sheet {
    width: 1200px; height: 930px;
    display: flex; align-items: center; justify-content: center; gap: 40px;
  }
  .card {
    width: 540px; height: 310px; position: relative;
    box-shadow: 0 6px 18px rgba(0,0,0,0.15);
  }
  /* Front */
  .card-front { background: var(--paper); }
  .brand-name {
    position: absolute; top: 48px; left: 200px; width: 300px;
    color: var(--brand-green); font-weight: 700; font-size: 34px;
    line-height: 1.05; letter-spacing: 1px; text-transform: uppercase;
  }
  .holder {
    position: absolute; top: 186px; left: 34px; width: 170px;
  }
  .holder-name {
    color: var(--brand-green); font-weight: 700; font-size: 17px;
    text-transform: uppercase; letter-spacing: 0.3px; white-space: nowrap;
  }
  .holder-title { color: var(--ink); font-size: 14px; margin-top: 3px; }
  .front-divider {
    position: absolute; top: 178px; left: 226px; width: 1px; height: 86px;
    background: var(--divider);
  }
  .contact-list {
    position: absolute; top: 180px; left: 246px; list-style: none;
  }
  .contact-list li {
    display: flex; align-items: center; gap: 9px;
    color: var(--ink); font-size: 15px; line-height: 21px;
  }
  .contact-icon { width: 13px; height: 13px; flex: none; }
  /* Back */
  .card-back { background: var(--brand-green); }
  .service-list {
    position: absolute; list-style: none;
    color: #ffffff; font-size: 13.5px; letter-spacing: 0.8px;
    text-transform: uppercase; line-height: 19px;
  }
  .service-list li { display: flex; align-items: center; gap: 10px; }
  .service-list li::before {
    content: ""; width: 6px; height: 6px; border-radius: 50%; background: #ffffff; flex: none;
  }
  .services-primary { top: 32px; left: 36px; }
  .services-secondary { top: 150px; left: 300px; }
</style>
</head>
<body>
<main class="sheet">
  <section class="card card-front" aria-label="Business card front">
    <div class="brand-name">Varkelt Construction Ltd</div>
    <div class="holder">
      <p class="holder-name">Tomasz Brelwik</p>
      <p class="holder-title">Managing Director</p>
    </div>
    <div class="front-divider"></div>
    <ul class="contact-list">
      <li>
        <svg class="contact-icon" viewBox="0 0 16 16"><path fill="var(--brand-green)" d="M3 1l3 3-1.5 2c1 2 3 4 5 5L11.5 9.5l3 3-2 2.5C7 14 2 9 1 3z"/></svg>
        020 5194 6281
      </li>
      <li>
        <svg class="contact-icon" viewBox="0 0 16 16"><rect x="4" y="1" width="8" height="14" rx="1.5" fill="none" stroke="var(--brand-green)" stroke-width="2"/></svg>
        07845139072
      </li>
      <li>
        <svg class="contact-icon" viewBox="0 0 16 16"><rect x="1" y="3" width="14" height="10" fill="var(--brand-green)"/><path d="M1 3l7 6 7-6" fill="none" stroke="#fff" stroke-width="1.4"/></svg>
        tomasz@varkelt.co.uk
      </li>
      <li>
        <svg class="contact-icon" viewBox="0 0 16 16"><circle cx="8" cy="8" r="7" fill="var(--brand-green)"/><path d="M1 8h14M8 1c-3 3-3 11 0 14M8 1c3 3 3 11 0 14" fill="none" stroke="#fff" stroke-width="1"/></svg>
        www.varkelt.co.uk
      </li>
    </ul>
  </section>

  <section class="card card-back" aria-label="Business card back">
    <ul class="service-list services-primary">
      <li>Kitchen Renovations</li>
      <li>Bathroom Renovations</li>
      <li>House Renovations</li>
      <li>Garage Conversions</li>
      <li>Extensions</li>
      <li>Loft Conversions</li>
      <li>Conservatories</li>
      <li>Carpentry</li>
    </ul>
    <ul class="service-list services-secondary">
      <li>Tiling</li>
      <li>Electrical</li>
      <li>Plumbing &amp; Heating</li>
      <li>Bricklaying</li>
      <li>Landscaping</li>
      <li>Decorating</li>
      <li>Plastering</li>
    </ul>
  </section>
</main>
</body>
</html>
```